complete redesign of VitalPlate.com

VITALPLATE.COM
MAIN MANU

We need it cut into HTML / Wordpress Friendly.... Our developer will handle all the WP / PHP coding, but we need it placed into HTML format so he can put into wordpress.

Please see the old vitalplate.com by visiting www.vitalplate.com... we want something completely different, but... just use this site for reference as to audience, theme, etc... we want something where it is science meets diet in helping fight cancer :)

WE NEED SOMETHING MORE MODERN AND MEDICAL IN TERMS OF DESIGN

See below:

1 CANCER NEWS
2 NUTRITION DIAGNOSTICS
3 DIET STEPS
4 DIET SUPPLEMENTS IN CANCER 
5 DICTIONARY OF MARKINGS ON FOOD
6 MERIBLEND VIDEOS
7 YOUR INDIVIDUAL DIET - SUBSCRIPTION

a. CANCER NEWS - latest articles relating to cancer prevention research treatments

b. NUTRITION DIAGNOSTICS -  description of the research that must be done to determine the degree of malnutrition of the body a place on the charts
pictures, etc.

c. DIET STEPS 
(sub menu - @)
¥ prevention of oncological - @
¥ diet chemotherapy - @
¥ diet in radiotherapy - @
¥ hormonal diet - @
¥ diet during convalescence - @

d. DIET SUPPLEMENTS IN CANCER - articles describing various supplements summary tables, etc.

e. DICTIONARY OF MARKINGS ON FOOD - composition, translation of labels on food, itd.

f. MERIBLEND VIDEOS 
(sub menu - @)
¥ healthy cooking - @
¥ meal preparation - @
¥ storage of food - @
¥ eco food - @
¥ rehabilitation - @
¥ yoga - @
¥ exercises - @
¥ psycho-oncology training - @
¥ music therapy - @

g. YOUR INDIVIDUAL DIET -  individual personalized diet for subscribing. We
add this point by developing a system of diet.

After 3 months, we will add special individual programs that mix diet, exercise and psychological lectures

Industry/Entity Type

Medical

Logo Text

Vital Plate / VitalPlate.com

Number of Pages Required

5+ page

Font styles to use
Sans Serif

Colors
ec1f27
9bcb3c
ffffff

Requirements
Must have
• HTML/CSS

```html
<!DOCTYPE html>
<html lang="en">
<head>
<meta charset="utf-8">
<title>VitalPlate — Science meets diet</title>
<link href="https://fonts.googleapis.com/css2?family=Fira+Sans:wght@300;400;500;600;700&display=swap" rel="stylesheet">
<style>
:root{
  --red:#e2001a;
  --blue:#1aa9e4;
  --navy:#1a4a8a;
  --ink:#222;
  --muted:#666;
  --white:#fff;
  --line:#f0f0f0;
}
*{box-sizing:border-box;margin:0;padding:0}
html,body{width:705px;height:1200px;overflow:hidden}
body{position:relative;background:var(--white);font-family:"Fira Sans",Arial,sans-serif;color:var(--ink)}
.abs{position:absolute}

/* header */
.brand{left:102px;top:16px;height:30px;display:flex;align-items:center;gap:8px}
.brand-dot{width:22px;height:22px;border-radius:50%;background:var(--red)}
.brand-name{font-size:17px;font-weight:600;color:var(--red)}
.connect{left:390px;top:27px;display:flex;align-items:center;gap:6px;font-size:6px;font-weight:500;color:#333}
.connect i{display:inline-block;width:9px;height:9px;border-radius:50%;background:#8a8a8a}
.phone{left:520px;top:25px;display:flex;align-items:center;gap:5px;font-size:10.5px;color:#222}

/* nav */
.main-nav{left:101px;top:53px;width:502px;height:29px;background:var(--red);display:flex}
.main-nav a{display:flex;align-items:center;justify-content:center;text-align:center;color:var(--white);text-decoration:none;font-size:6px;line-height:8px;font-weight:500;border-right:1px solid rgba(255,255,255,.25)}
.main-nav a:last-child{border-right:0}

/* hero */
.hero{left:0;top:82px;width:705px;height:228px;background:radial-gradient(ellipse at 40% 20%,#cfc6c6 0%,#9e9696 45%,#5e5a5c 100%)}
.hero-title{left:246px;top:185px;width:210px;height:41px;background:rgba(30,30,30,.75);color:var(--white);font-size:28px;font-weight:300;letter-spacing:1px;display:flex;align-items:center;justify-content:center}
.hero-dots{left:316px;top:283px;display:flex;gap:4px}
.hero-dots span{width:6px;height:6px;border-radius:50%;background:var(--white)}
.hero-dots span:first-child{background:var(--blue)}

/* section heads */
.block-head{height:46px;color:var(--white);font-size:13px;font-weight:500;line-height:16px;padding:8px 0 0 9px}
.news-head{left:101px;top:334px;width:287px;background:var(--red)}
.video-head{left:402px;top:334px;width:201px;background:var(--blue);padding-left:12px}
.arrows{position:absolute;right:12px;top:16px}

/* news */
.news-img{left:101px;width:114px;height:82px}
.news-body{left:223px;width:166px}
.news-meta{font-size:4.5px;color:var(--muted);letter-spacing:.2px}
.news-meta b{color:#111;font-weight:500}
.news-title{margin-top:7px;font-size:6px;line-height:10px;font-weight:600;color:var(--navy)}
.news-text{margin-top:2px;font-size:5.3px;line-height:10.5px;color:#222}
.read-more{display:inline-block;margin-top:5px;background:var(--red);color:var(--white);font-size:5.5px;font-weight:600;padding:3px 4px}
.all-articles{left:101px;top:716px;width:287px;height:28px;background:var(--blue);color:var(--white);font-size:8px;display:flex;align-items:center;justify-content:center}

/* videos */
.video{left:402px;width:201px;height:106px}
.play{position:absolute;left:50%;top:50%;margin:-9px 0 0 -9px}
.video-caption{position:absolute;left:9px;bottom:8px;color:var(--white);font-size:7px;font-weight:600;letter-spacing:.2px}

/* diet steps */
.steps{left:0;top:786px;width:705px;height:199px;background:var(--red)}
.steps-title{left:0;top:809px;width:705px;text-align:center;color:var(--white);font-size:13px;font-weight:500}
.steps-menu{left:102px;top:839px;width:115px;height:112px;background:var(--white);list-style:none}
.steps-menu li{height:22.4px;display:flex;align-items:center;padding-left:11px;font-size:5.5px;color:#555;border-bottom:1px solid var(--line)}
.steps-menu li.active{background:var(--blue);color:var(--white);font-weight:600}
.steps-img{left:230px;top:839px;width:165px;height:112px;background:radial-gradient(circle at 45% 45%,#b45a2c 0%,#6e2a18 35%,#2b1510 75%)}
.steps-text{left:402px;top:839px;width:202px;color:var(--white);font-size:5.3px;line-height:10.5px}
.steps-text p+p{margin-top:10px}

/* subscribe */
.subscribe{left:0;top:985px;width:705px;height:150px;background:var(--blue)}
.sub-title{left:0;top:1011px;width:705px;text-align:center;color:var(--white);font-size:18px;font-weight:600}
.sub-text{left:140px;top:1044px;width:425px;text-align:center;color:var(--white);font-size:5.3px;line-height:10.5px}
.sub-input{left:186px;top:1085px;width:245px;height:21px;background:var(--white);font-size:5.5px;color:#888;padding-left:6px;display:flex;align-items:center}
.sub-btn{left:444px;top:1085px;width:74px;height:21px;background:var(--red);color:var(--white);font-size:6px;font-weight:600;display:flex;align-items:center;justify-content:center}

/* footer */
.foot-nav{left:0;top:1154px;width:705px;display:flex;justify-content:center;font-size:5.8px;color:#111}
.foot-nav span{padding:0 5px}
.copy{left:0;top:1175px;width:705px;text-align:center;font-size:5.8px;color:#111}
</style>
</head>
<body>

<header>
  <div class="abs brand"><span class="brand-dot"></span><span class="brand-name">VitalPlate</span></div>
  <div class="abs connect">CONNECT WITH US <i></i><i></i><i></i><i></i></div>
  <div class="abs phone">
    <svg width="8" height="8" viewBox="0 0 24 24"><path fill="#1aa9e4" d="M6.6 10.8a15 15 0 0 0 6.6 6.6l2.2-2.2c.3-.3.7-.4 1-.2 1.1.4 2.3.6 3.6.6.6 0 1 .4 1 1V20c0 .6-.4 1-1 1A17 17 0 0 1 3 4c0-.6.4-1 1-1h3.5c.6 0 1 .4 1 1 0 1.3.2 2.5.6 3.6.1.3 0 .7-.2 1z"/></svg>
    1-800-555-0147
  </div>
  <nav class="abs main-nav">
    <a style="width:48px">CANCER<br>NEWS</a>
    <a style="width:65px">NUTRITION<br>DIAGNOSTICS</a>
    <a style="width:47px">DIET<br>STEPS</a>
    <a style="width:101px">DIET SUPPLEMENTS<br>IN CANCER</a>
    <a style="width:104px">DICTIONARY OF<br>MARKINGS ON FOOD</a>
    <a style="width:46px">MERIBLEND<br>VIDEOS</a>
    <a style="width:91px">YOUR INDIVIDUAL<br>DIET -SUBSCRIPTION</a>
  </nav>
</header>

<section>
  <div class="abs hero" role="img" aria-label="Microscopic 3D view of cells and dark virus particles on a tissue surface"></div>
  <div class="abs hero-title">VITAL PLATE</div>
  <div class="abs hero-dots"><span></span><span></span><span></span><span></span></div>
</section>

<section>
  <div class="abs block-head news-head">VITAL PLATE<br>NEWS</div>

  <div class="abs news-img" style="top:398px;background:linear-gradient(135deg,#a88a5a,#6e5434)" role="img" aria-label="Potatoes with the word cancer spelled in peel"></div>
  <div class="abs news-body" style="top:397px">
    <div class="news-meta">DECEMBER 15TH, 2015 &nbsp;|&nbsp; <b>POSTED BY VITAL PLATE</b></div>
    <div class="news-title">LOREM IPSUM IS SIMPLY DUMMY TEXT OF THE PRINTING AND TYPESETTING INDUSTRY.</div>
    <div class="news-text">&nbsp;Lorem Ipsum has been the industry's standard dummy text ever since the 1500s, when an unknown printer took a galley of type and scrambled it to make a type specimen book.</div>
    <span class="read-more">READ MORE</span>
  </div>

  <div class="abs news-img" style="top:510px;background:linear-gradient(135deg,#c0502a,#7a3a1e 60%,#c9c3b6)" role="img" aria-label="Plate of vegetable rice dish"></div>
  <div class="abs news-body" style="top:508px">
    <div class="news-meta">DECEMBER 15TH, 2015 &nbsp;|&nbsp; <b>POSTED BY VITAL PLATE</b></div>
    <div class="news-title">LOREM IPSUM IS SIMPLY DUMMY TEXT OF THE PRINTING AND TYPESETTING INDUSTRY.</div>
    <div class="news-text">&nbsp;Lorem Ipsum has been the industry's standard dummy text ever since the 1500s, when an unknown printer took a galley of type and scrambled it to make a type specimen book.</div>
    <span class="read-more">READ MORE</span>
  </div>

  <div class="abs news-img" style="top:621px;background:linear-gradient(135deg,#c8202a,#8a1a2a 55%,#3a3a6a)" role="img" aria-label="Strawberries, blueberries and supplement capsules"></div>
  <div class="abs news-body" style="top:619px">
    <div class="news-meta">DECEMBER 15TH, 2015 &nbsp;|&nbsp; <b>POSTED BY VITAL PLATE</b></div>
    <div class="news-title">LOREM IPSUM IS SIMPLY DUMMY TEXT OF THE PRINTING AND TYPESETTING INDUSTRY.</div>
    <div class="news-text">&nbsp;Lorem Ipsum has been the industry's standard dummy text ever since the 1500s, when an unknown printer took a galley of type and scrambled it to make a type specimen book.</div>
    <span class="read-more">READ MORE</span>
  </div>

  <div class="abs all-articles">VIEW LATEST ARTICLES</div>
</section>

<section>
  <div class="abs block-head video-head">MERIBLEND<br>VIDEOS
    <svg class="arrows" width="20" height="12" viewBox="0 0 20 12"><path d="M6 1 1 6l5 5M14 1l5 5-5 5" fill="none" stroke="#fff" stroke-width="2"/></svg>
  </div>

  <div class="abs video" style="top:398px;background:linear-gradient(135deg,#8a7a5a,#b89a6a 50%,#5a7a3a)" role="img" aria-label="Bowls of fresh salad on burlap">
    <svg class="play" width="18" height="18" viewBox="0 0 18 18"><circle cx="9" cy="9" r="8" fill="none" stroke="#fff" stroke-width="1.6"/><path d="M7 5.5v7l5.5-3.5z" fill="#fff"/></svg>
    <span class="video-caption">HEALTHY COOKING - @</span>
  </div>
  <div class="abs video" style="top:518px;background:linear-gradient(135deg,#d8dadc,#9aa0a8 60%,#5a6470)" role="img" aria-label="Couple preparing a meal in a kitchen">
    <svg class="play" width="18" height="18" viewBox="0 0 18 18"><circle cx="9" cy="9" r="8" fill="none" stroke="#fff" stroke-width="1.6"/><path d="M7 5.5v7l5.5-3.5z" fill="#fff"/></svg>
    <span class="video-caption">MEAL PREPARATION - @</span>
  </div>
  <div class="abs video" style="top:638px;background:linear-gradient(135deg,#3a1a0a,#c0651a 55%,#7a3a10)" role="img" aria-label="Glass jars of preserved food">
    <svg class="play" width="18" height="18" viewBox="0 0 18 18"><circle cx="9" cy="9" r="8" fill="none" stroke="#fff" stroke-width="1.6"/><path d="M7 5.5v7l5.5-3.5z" fill="#fff"/></svg>
    <span class="video-caption">STORAGE OF FOOD</span>
  </div>
</section>

<section>
  <div class="abs steps"></div>
  <h2 class="abs steps-title">DIET STEPS</h2>
  <ul class="abs steps-menu">
    <li class="active">PREVENTION OF ONCOLOGICAL - @</li>
    <li>DIET CHEMOTHERAPY - @</li>
    <li>DIET IN RADIOTHERAPY - @</li>
    <li>HORMONAL DIET - @</li>
    <li>DIET DURING CONVALESCENCE - @</li>
  </ul>
  <div class="abs steps-img" role="img" aria-label="Illustration of a cancer cell surrounded by immune cells"></div>
  <div class="abs steps-text">
    <p>Lorem Ipsum is simply dummy text of the printing and typesetting industry. Lorem Ipsum has been the industry's standard dummy text ever since the 1500s, when an unknown printer took a galley of type and scrambled it to make a type specimen book. It has survived not only five centuries, but also the leap into electronic typesetting, remaining essentially unchanged.</p>
    <p>It was popularised in the 1960s with the release of Glyphset sheets containing Lorem Ipsum passages, and more recently with desktop publishing software like Pagecraft Studio including versions of Lorem Ipsum.</p>
  </div>
</section>

<section>
  <div class="abs subscribe"></div>
  <h2 class="abs sub-title">YOUR INDIVIDUAL DIET</h2>
  <p class="abs sub-text">individual personalized diet for subscribing. We add this point by developing a system of diet.After 3 months, we will add special individual programs that mix diet, exercise and psychological lectures</p>
  <div class="abs sub-input">Enter Your E-Mail Address</div>
  <div class="abs sub-btn">SUBSCRIBE NOW</div>
</section>

<footer>
  <div class="abs foot-nav"><span>CANCER NEWS</span>|<span>DIET STEPS</span>|<span>4 DIET SUPPLEMENTS IN CANCER</span>|<span>DICTIONARY OF MARKINGS ON FOOD</span>|<span>MERIBLEND VIDEOS</span>|<span>YOUR INDIVIDUAL DIET - SUBSCRIPTION</span></div>
  <div class="abs copy">© COMPANY NAME &nbsp;| ALL RIGHTS RESERVED</div>
</footer>

</body>
</html>
```